Coffeeshop menu for filter tip

We want to have a cannabis (coffeeshop) menu in the size 25mm wide x 60mm wide. Some examples attached.

it must have the following text:
Menu

WEED p/g
Oblivane €16
Cloudplum €14
Tide Runner €14
Quincefig €16
Mega Marsh €14
Grey Heron €14

HASH p/g
Tashar Amber €12
Pebble Frost€11
Lime Dunes €14
Ash Petal €10

Target Market(s)

tourist in Amsterdam

Requirements
Nice to have
• cannabis sign leaf
• No Cigarettes allowed symbol

```html
<!DOCTYPE html>
<html lang="en">
<head>
<meta charset="utf-8">
<title>Coffeeshop Menu – Filter Tip</title>
<link rel="stylesheet" href="https://fonts.googleapis.com/css2?family=Oswald:wght@700&family=Ultra&family=Germania+One&family=Metamorphous&family=Lobster&family=Caveat+Brush&family=Kaushan+Script&family=Lobster+Two:ital,wght@1,700&family=UnifrakturMaguntia&family=Pirata+One&family=Sniglet:wght@800&display=swap">
<style>
  :root {
    --page: #ffffff;
    --leaf-green: #1f8a45;
    --leaf-green-dark: #0f6b34;
    --gold: #e9d58f;
    --gold-deep: #b8964a;
    --panel-dark: #3a1c0c;
    --panel-mid: #5a250f;
    --panel-glow: #9b1f1f;
    --heading-green: #3fae3f;
    --menu-white: #ffffff;
  }
  * { margin: 0; padding: 0; box-sizing: border-box; }
  html, body { width: 750px; height: 1200px; overflow: hidden; background: var(--page); }
  .canvas { position: relative; width: 750px; height: 1200px; }

  .menu-title {
    position: absolute; width: 1px; height: 1px; overflow: hidden;
    clip: rect(0 0 0 0); white-space: nowrap;
  }

  .menu-strip {
    position: absolute; left: 185px; top: 159px; width: 355px; height: 886px;
    box-shadow: 2px 3px 4px rgba(0,0,0,0.25);
  }
  .leaf-backdrop {
    position: absolute; inset: 0;
    background: radial-gradient(circle at 50% 50%, var(--leaf-green) 0%, var(--leaf-green-dark) 100%);
  }

  .menu-panel { position: absolute; left: 21px; width: 313px; }
  .menu-panel--weed { top: 41px; height: 413px; }
  .menu-panel--hash { top: 510px; height: 331px; }

  .filigree-border {
    position: absolute; inset: 0; border-radius: 14px;
    background: linear-gradient(135deg, var(--gold) 0%, var(--gold-deep) 50%, var(--gold) 100%);
  }
  .panel-field {
    position: absolute; inset: 20px; border-radius: 8px;
    background: radial-gradient(ellipse at 50% 50%, var(--panel-glow) 0%, var(--panel-mid) 45%, var(--panel-dark) 100%);
  }

  .section-title {
    position: absolute; left: 0; right: 0; text-align: center;
    font-family: "Oswald", sans-serif; font-weight: 700;
    color: var(--heading-green); font-size: 40px; line-height: 1;
  }
  .section-title .unit { font-size: 22px; }

  .menu-item {
    position: absolute; left: 36px; right: 34px;
    display: flex; justify-content: space-between; align-items: baseline; gap: 8px;
    color: var(--menu-white); line-height: 1; white-space: nowrap;
  }
  .menu-item .price { font-family: "Metamorphous", serif; font-size: 21px; }

  .strain--oblivane   { font-family: "Ultra", serif; font-size: 25px; }
  .strain--cloudplum  { font-family: "Germania One", serif; font-size: 31px; }
  .strain--tiderunner { font-family: "Metamorphous", serif; font-size: 21px; text-transform: uppercase; }
  .strain--quincefig  { font-family: "Lobster", cursive; font-size: 29px; }
  .strain--megamarsh  { font-family: "Caveat Brush", cursive; font-size: 32px; }
  .strain--greyheron  { font-family: "Kaushan Script", cursive; font-size: 26px; }
  .strain--tashar     { font-family: "Lobster Two", cursive; font-style: italic; font-weight: 700; font-size: 26px; }
  .strain--pebble     { font-family: "UnifrakturMaguntia", cursive; font-size: 28px; }
  .strain--lime       { font-family: "Pirata One", cursive; font-size: 28px; }
  .strain--ash        { font-family: "Sniglet", sans-serif; font-weight: 800; font-size: 24px; }
</style>
</head>
<body>
<div class="canvas">
  <main class="menu-strip">
    <h1 class="menu-title">Menu</h1>
    <div class="leaf-backdrop" role="img" aria-label="Green background pattern of cannabis leaves"></div>

    <section class="menu-panel menu-panel--weed">
      <div class="filigree-border" role="img" aria-label="Gold filigree ornamental frame"></div>
      <div class="panel-field"></div>
      <h2 class="section-title" style="top:48px;">WEED <span class="unit">p/g</span></h2>
      <div class="menu-item" style="top:114px;"><span class="strain--oblivane">Oblivane</span><span class="price">€16</span></div>
      <div class="menu-item" style="top:158px;"><span class="strain--cloudplum">Cloudplum</span><span class="price">€14</span></div>
      <div class="menu-item" style="top:206px;"><span class="strain--tiderunner">Tide Runner</span><span class="price">€14</span></div>
      <div class="menu-item" style="top:247px;"><span class="strain--quincefig">Quincefig</span><span class="price">€16</span></div>
      <div class="menu-item" style="top:289px;"><span class="strain--megamarsh">Mega Marsh</span><span class="price">€14</span></div>
      <div class="menu-item" style="top:338px;"><span class="strain--greyheron">Grey Heron</span><span class="price">€14</span></div>
    </section>

    <section class="menu-panel menu-panel--hash">
      <div class="filigree-border" role="img" aria-label="Gold filigree ornamental frame"></div>
      <div class="panel-field"></div>
      <h2 class="section-title" style="top:52px;">HASH <span class="unit">p/g</span></h2>
      <div class="menu-item" style="top:113px;"><span class="strain--tashar">Tashar Amber</span><span class="price">€12</span></div>
      <div class="menu-item" style="top:158px;"><span class="strain--pebble">Pebble Frost</span><span class="price">€11</span></div>
      <div class="menu-item" style="top:203px;"><span class="strain--lime">Lime Dunes</span><span class="price">€14</span></div>
      <div class="menu-item" style="top:249px;"><span class="strain--ash">Ash Petal</span><span class="price">€10</span></div>
    </section>
  </main>
</div>
</body>
</html>
```